Real estate broker business card

Want a modern celan but effective business card for my residential and commercial real estate business. I want the back of the card to advertise my services and to capture business. I have attached the back of my current business card fore ideas
Updates

Logos, photo and text updates added! Added Saturday, September 3, 2016

Project Deadline Extended Reason: LOGOS, PHOTOS AND TEST JUST UPLOADED! I'M READY TO PICK A DESIGN! THANK YOU! Added Saturday, September 3, 2016

Target Market(s)

home buyers and seller. commercial buyers and sellers

Industry/Entity Type

Real Estate

Contact Information for Business Card

must have my contact information and my photo

Requirements
Must have
• Carla Ventrino
• Owner & Qualifying Broker
• Ventrino Real Estate Services
• 505.718.2094
• carla@ventrinohomes.example
• www.ventrinohomes.example
Nice to have
• metallic
• Business capture text: " Don't buy or lease property without someone looking out for your best interests. I will represent you on your home or investment purchase for FREE!"
• "Home owners, call today to receive a FREE market analysis for your homes value!

```html
<!DOCTYPE html>
<html lang="en">
<head>
<meta charset="UTF-8">
<title>Ventrino Real Estate Services – Business Card</title>
<link href="https://fonts.googleapis.com/css2?family=Open+Sans:wght@400;600&display=swap" rel="stylesheet">
<style>
  :root {
    --backdrop: #3a3532;
    --card: #0d0d0e;
    --card-edge: #1b1b1d;
    --teal: #2f8a99;
    --teal-light: #3fa3b3;
    --text: #e9e9e9;
    --photo-dark: #2a211d;
    --photo-light: #d9d3cc;
  }
  * { margin: 0; padding: 0; box-sizing: border-box; }
  html, body {
    width: 1200px; height: 900px; overflow: hidden;
    background: var(--backdrop);
    font-family: "Open Sans", Arial, sans-serif;
  }
  .canvas {
    position: relative; width: 1200px; height: 900px;
    display: flex; align-items: center; justify-content: center; gap: 60px;
  }
  .card {
    position: relative; width: 520px; height: 298px;
    background: radial-gradient(ellipse at 60% 30%, var(--card-edge), var(--card) 70%);
    border-radius: 4px;
    box-shadow: 0 14px 30px rgba(0,0,0,.45);
    overflow: hidden;
  }

  /* Front */
  .portrait {
    position: absolute; left: 0; bottom: 0; width: 250px; height: 215px;
    border-top-right-radius: 120px 110px;
    background: linear-gradient(180deg, var(--photo-dark) 0%, #6b4d40 40%, var(--photo-light) 100%);
  }
  .wordmark {
    color: var(--teal); font-weight: 600; letter-spacing: .06em;
    text-transform: uppercase;
  }
  .front .wordmark {
    position: absolute; left: 282px; top: 30px; width: 220px;
    font-size: 15px; line-height: 20px;
  }
  .divider {
    position: absolute; left: 264px; top: 118px; width: 1px; height: 120px;
    background: var(--teal);
  }
  .identity { position: absolute; left: 282px; top: 100px; }
  .name { color: var(--teal-light); font-weight: 600; font-size: 16px; }
  .title { color: var(--text); font-size: 12.5px; margin-top: 2px; }
  .contact {
    position: absolute; left: 282px; top: 168px; list-style: none;
    color: var(--text); font-size: 12.5px;
  }
  .contact li { display: flex; align-items: center; gap: 8px; line-height: 20px; white-space: nowrap; }
  .contact svg { width: 11px; height: 11px; fill: var(--teal-light); flex: none; }

  /* Back */
  .back { display: flex; align-items: center; justify-content: center; }
  .back .brand { display: flex; align-items: center; gap: 14px; }
  .brand-square { width: 46px; height: 46px; background: var(--teal); border-radius: 3px; }
  .back .wordmark { font-size: 20px; white-space: nowrap; }
</style>
</head>
<body>
<main class="canvas">
  <section class="card front" aria-label="Card front">
    <div class="portrait" role="img" aria-label="Portrait photo of Carla Ventrino in a white lace top"></div>
    <div class="wordmark">Ventrino<br>Real Estate Services</div>
    <div class="divider"></div>
    <div class="identity">
      <div class="name">Carla Ventrino</div>
      <div class="title">Owner &amp; Qualifying Broker</div>
    </div>
    <ul class="contact">
      <li>Ventrino Real Estate Services</li>
      <li><svg viewBox="0 0 24 24"><path d="M6.6 10.8a15.1 15.1 0 0 0 6.6 6.6l2.2-2.2c.3-.3.7-.4 1-.2 1.1.4 2.3.6 3.6.6.6 0 1 .4 1 1V20c0 .6-.4 1-1 1A17 17 0 0 1 3 4c0-.6.4-1 1-1h3.5c.6 0 1 .4 1 1 0 1.3.2 2.5.6 3.6.1.3 0 .7-.2 1z"/></svg>505.718.2094</li>
      <li><svg viewBox="0 0 24 24"><path d="M2 5h20v2l-10 7L2 7z"/><path d="M2 9l10 7 10-7v10H2z"/></svg>carla@ventrinohomes.example</li>
      <li><svg viewBox="0 0 24 24"><circle cx="12" cy="12" r="10"/><path d="M2 12h20M12 2c3 3 3 17 0 20M12 2c-3 3-3 17 0 20" stroke="#0d0d0e" stroke-width="1.5" fill="none"/></svg>www.ventrinohomes.example</li>
    </ul>
  </section>

  <section class="card back" aria-label="Card back">
    <div class="brand">
      <div class="brand-square"></div>
      <div class="wordmark">Ventrino Real Estate Services</div>
    </div>
  </section>
</main>
</body>
</html>
```